Visitenkarten-Design für virtuelle Jobmesse & Jobbörse für Soldaten
Zielgruppe
Die KVL GmbH ist ein Unternehmen das zwei Hauptprodukte betreibt! Zum einen Jobbörse für Soldaten unter www.laufbahnwechsel-beispiel.de und zum anderen eine virtuelle Jobmesse für Soldaten unter www.merivon-beispiel.de , die wir zweimal im Jahr veranstalten.
Aufgabenstellung
Wir haben ja die beiden Produkte Laufbahnwechsel.de und die Merivon, für die bereits jeweils ein separtes Logo besteht! Diese finden Sie im Anhang! Beide werden doch jedoch von einem Unternehmen, der KVL GmbH betrieben! Aktuell nutzen wir eine Visitenkarte mit dem Logo von KVL und eine mit dem Logo der MERIVON. Gerade im Hinblick darauf, dass wir zukünftig auch weiter Plattformen in unser Portfolio aufnehmen, möchte ich hier unsere V-Karten flexibler gestalten!
Ziel soll es also sein, eine Visitenkarte zu gestalten, auf dem klar wird, dass der Mitarbeiter von der KVL GmbH kommt, die KVL GmbH aber unterschiedliche Produkte betreibt.
Im Anhang finden Sie:
1. Das Logo von KVL
2. Das Logo von Merivon
3. Die aktuelle V-Karte von KVL
4. Die aktuelle V-Karte von MERIVON
Vielleicht ein kleiner Anreiz: Aktuell nutzen wir auch zwei getrennte Geschäftspapiere. Das von www.laufbahnwechsel-beispiel.de lade ich einmal hoch! Der Designer, der auch die Visitenkarte erstellt, erhällt im Anschluss den 1:1 Auftrag in Höhe von 200 Euro für die Erstellung des Geschäftspapiers! Wenn Sie jetzt schon einen Vorschlag für das Geschäftspapier einreichen, erhöht das natürlich Ihre Chancen, wobei ich verspreche, dass wir im Falle eine Annahme das 1:1 im Anschluß dennoch starten werden!

```html
<!DOCTYPE html>
<html lang="de">
<head>
<meta charset="utf-8">
<title>Visitenkarten KVL GmbH</title>
<link href="https://fonts.googleapis.com/css2?family=Arimo:wght@400;700&display=swap" rel="stylesheet">
<style>
  :root {
    --page: #d9dbdd;
    --card: #f1f1f1;
    --navy: #1d3f7f;
    --green: #3a5a22;
    --grey-line: #8a8a8a;
    --text: #3a3a3a;
    --mark-grey: #7b7b7b;
  }
  * { box-sizing: border-box; margin: 0; padding: 0; }
  html, body { width: 1200px; height: 900px; overflow: hidden; }
  body {
    background: var(--page);
    font-family: "Arimo", Arial, sans-serif;
    color: var(--text);
    position: relative;
  }
  .card {
    position: absolute;
    width: 530px;
    height: 343px;
    background: linear-gradient(180deg, #f6f6f6, #e9e9e9);
    box-shadow: 0 6px 18px rgba(0,0,0,.18);
    overflow: hidden;
  }
  .card--back-plain   { left: 50px;  top: 87px; }
  .card--front-wide   { left: 620px; top: 87px; }
  .card--front-stack  { left: 50px;  top: 470px; }
  .card--back-brand   { left: 620px; top: 470px; }

  .rule {
    position: absolute;
    height: 5px;
    border-top: 2px solid var(--navy);
    border-bottom: 1px solid var(--grey-line);
  }
  .brand-mark {
    position: absolute;
    display: flex;
    align-items: center;
    gap: 10px;
    color: var(--navy);
    font-weight: 700;
    background: var(--card);
    padding: 0 12px;
  }
  .brand-mark__square {
    width: 18px; height: 18px;
    background: var(--mark-grey);
  }
  .product-mark {
    position: absolute;
    color: var(--green);
    font-weight: 700;
    display: flex;
    align-items: center;
    gap: 6px;
  }
  .product-mark__dot {
    width: 10px; height: 10px; border-radius: 50%;
    background: var(--green);
  }
  .product-note {
    position: absolute;
    font-size: 11px;
    color: #555;
    line-height: 1.25;
  }
  .company { font-weight: 700; color: #333; }
  .person__name { color: var(--navy); font-weight: 700; font-size: 22px; }
  .person__role { font-size: 13px; color: #444; margin-top: 2px; }
  .contact { font-size: 12px; line-height: 1.45; color: #333; }

  .band {
    position: absolute;
    left: 0; right: 0; bottom: 0;
    height: 30px;
    display: flex;
    justify-content: space-between;
    align-items: center;
    padding: 0 20px;
    color: #fff;
    font-weight: 700;
    font-size: 13px;
  }
  .band--green-blue { background: linear-gradient(90deg, var(--green) 0%, var(--green) 25%, var(--navy) 80%); }
  .band--blue-green { background: linear-gradient(90deg, var(--navy) 0%, var(--navy) 20%, var(--green) 85%); height: 24px; }
</style>
</head>
<body>

  <!-- Rückseite, nur Marke -->
  <section class="card card--back-plain">
    <div class="rule" style="left:0; right:0; top:170px;"></div>
    <div class="brand-mark" style="left:50%; top:158px; transform:translateX(-50%); font-size:26px;">
      <span class="brand-mark__square"></span>Laufbahnwechsel.de
    </div>
  </section>

  <!-- Vorderseite, Querformat-Variante -->
  <section class="card card--front-wide">
    <div class="rule" style="left:0; width:330px; top:116px;"></div>
    <div class="brand-mark" style="right:14px; top:18px; font-size:17px; flex-direction:column; align-items:flex-end; gap:4px; background:none;">
      <span style="display:flex; align-items:center; gap:8px;"><span class="brand-mark__square"></span>Laufbahnwechsel.de</span>
      <span class="company" style="font-size:18px;">KVL GmbH</span>
    </div>
    <div class="product-mark" style="right:20px; top:90px; font-size:15px;">
      <span class="product-mark__dot"></span>Merivon.de
    </div>
    <div class="product-note" style="right:20px; top:112px; font-weight:700; color:var(--green);">ist eine Marke der KVL GmbH</div>

    <div class="person" style="position:absolute; left:34px; top:170px;">
      <div class="person__name">Jonas Weber</div>
      <div class="person__role">Geschäftsführer</div>
    </div>

    <div class="contact" style="position:absolute; right:20px; top:200px; text-align:right;">
      Lindenweg 7 • 80000 Musterstadt<br>
      Telefon: 0800 - 123 45 67 • Mobil: 0170 - 000 11 222<br>
      jonas.weber@merivon-beispiel.de • jonas.weber@laufbahnwechsel-beispiel.de
    </div>

    <div class="band band--green-blue">
      <span>www.merivon-beispiel.de</span>
      <span>www.laufbahnwechsel-beispiel.de</span>
    </div>
  </section>

  <!-- Vorderseite, Spalten-Variante -->
  <section class="card card--front-stack">
    <div class="rule" style="left:0; right:0; top:54px;"></div>
    <div class="brand-mark" style="left:18px; top:40px; font-size:16px;">
      <span class="brand-mark__square"></span>Laufbahnwechsel.de
    </div>
    <div class="product-mark" style="right:30px; top:22px; font-size:16px; background:var(--card); padding:0 8px;">
      <span class="product-mark__dot"></span>Merivon.de
    </div>
    <div class="product-note" style="right:38px; top:68px; text-align:center;">ist eine Marke der<br>KVL GmbH</div>

    <div style="position:absolute; left:32px; top:90px;">
      <div class="company" style="font-size:22px;">KVL GmbH</div>
      <div class="contact" style="font-size:14px; margin-top:2px;">Lindenweg 7<br>80000 Musterstadt</div>
      <div class="contact" style="font-size:14px; margin-top:14px;">
        Telefon: 0800 - 123 45 67<br>
        Mobil: &nbsp;&nbsp;&nbsp;0170 - 000 11 222<br>
        jonas.weber@laufbahnwechsel-beispiel.de<br>
        jonas.weber@merivon-beispiel.de
      </div>
    </div>

    <div class="person" style="position:absolute; right:40px; top:132px; text-align:left;">
      <div class="person__name" style="font-size:24px;">Jonas Weber</div>
      <div class="person__role">Geschäftsführer</div>
    </div>

    <div class="band band--blue-green"></div>
  </section>

  <!-- Rückseite mit Produktmarke -->
  <section class="card card--back-brand">
    <div class="rule" style="left:0; right:0; top:134px;"></div>
    <div class="brand-mark" style="left:50%; top:120px; transform:translateX(-50%); font-size:26px;">
      <span class="brand-mark__square"></span>Laufbahnwechsel.de
    </div>
    <div class="product-mark" style="left:50%; top:178px; transform:translateX(-50%); font-size:16px;">
      <span class="product-mark__dot"></span>Merivon.de
    </div>
    <div class="product-note" style="left:50%; top:200px; transform:translateX(-50%); text-align:center;">ist eine Marke der<br>KVL GmbH</div>

    <div class="band band--green-blue">
      <span>www.merivon-beispiel.de</span>
      <span>www.laufbahnwechsel-beispiel.de</span>
    </div>
  </section>

</body>
</html>
```